Garland Custom Boats Website update

I would like an updated website to my current site (Garlandboats.com).
I have an updated logo i would like to incorporate.
24 pages , would like to integrate videos of the boats (that i can upload later)

Target Market(s)

Professional and Commercial boat owners

Industry/Entity Type

Custom Boat Manufacturing

Coding

Coded - Design and coding required

Number of Pages Required

5+ page

Font styles to use
Serif

Requirements
Must have
• Easy to read, well laid-out, and video integration
Nice to have
• Fresh up to date look

```html
<!DOCTYPE html>
<html lang="en">
<head>
<meta charset="utf-8">
<title>Garland Custom Boats</title>
<link rel="stylesheet" href="https://fonts.googleapis.com/css2?family=Chakra+Petch:ital,wght@0,600;0,700;1,700&family=Figtree:wght@400;500;600&display=swap">
<style>
:root{
  --navy:#0a3aa0;
  --navy-deep:#08328c;
  --red:#c8202a;
  --ink:#222;
  --muted:#555;
  --pale:#eef2fa;
  --black:#000;
  --white:#fff;
}
*{box-sizing:border-box;margin:0;padding:0}
html,body{width:1200px;height:4023px;overflow:hidden;background:var(--white)}
body{position:relative;font-family:'Figtree',sans-serif;color:var(--ink)}
.abs{position:absolute}
.heading{font-family:'Chakra Petch',sans-serif;font-style:italic;font-weight:700;font-size:40px;letter-spacing:.5px;color:var(--navy);line-height:1}
.heading .accent{color:var(--red)}
.underline{height:4px;width:160px;background:var(--red);border-radius:50%}
.btn{display:inline-flex;align-items:center;justify-content:center;font-family:'Chakra Petch',sans-serif;font-weight:700;font-size:17px;color:var(--white);background:var(--navy);border-radius:0 24px 0 0;transform:skewX(-8deg)}
.btn span{transform:skewX(8deg)}
.photo{background:linear-gradient(160deg,#8fb6d8,#2f6aa1 55%,#123f73)}
/* header */
.brand{left:110px;top:20px;font-family:'Chakra Petch',sans-serif;font-weight:700;font-size:26px;color:var(--navy);line-height:1}
.brand small{display:block;font-size:13px;font-weight:600;letter-spacing:2px;color:var(--navy);margin-top:4px}
.nav{top:33px;font-size:15px;color:#333}
.nav.active{color:var(--red);font-weight:600}
/* hero */
.hero{left:0;top:84px;width:1200px;height:549px;background:radial-gradient(ellipse at 75% 45%,#3b7fc0,#0d4a8a 50%,#062f63)}
.hero h1{left:110px;top:200px;font-family:'Chakra Petch',sans-serif;font-weight:700;font-size:56px;line-height:64px;color:var(--white)}
.hero p{left:110px;top:332px;width:470px;font-size:17px;line-height:28px;color:var(--white)}
/* text */
.body-text{font-size:15px;line-height:26px;color:#333}
.label{font-family:'Chakra Petch',sans-serif;font-weight:700;font-size:19px;color:var(--white);text-align:center;width:303px}
.card{width:303px;height:298px;border:3px solid var(--white)}
.partner{width:193px;height:93px;background:var(--white);display:flex;align-items:center;justify-content:center}
.partner i{display:block;width:110px;height:34px;border-radius:6px;background:#d9dde6}
.field{background:var(--white);border-radius:6px;box-shadow:0 4px 10px rgba(0,0,0,.08);border:1px solid #e6e8ee;font-size:14px;color:#777;padding:16px 16px}
/* footer */
.footer{left:0;top:3575px;width:1200px;height:448px;background:var(--black)}
.ftitle{font-family:'Figtree',sans-serif;font-weight:600;font-size:21px;color:var(--white)}
.flink{font-size:15px;color:var(--white);display:flex;align-items:center;gap:12px;height:31px}
.social{width:30px;height:30px;border-radius:50%;border:1.5px solid var(--white)}
.ficon{width:36px;height:36px;border-radius:50%;background:var(--red);display:flex;align-items:center;justify-content:center}
</style>
</head>
<body>

<!-- header -->
<div class="abs brand">GARLAND<small>CUSTOM BOATS</small></div>
<div class="abs nav active" style="left:454px">Home</div>
<div class="abs nav" style="left:520px">About Us</div>
<div class="abs nav" style="left:609px">Harbor Patrol Package</div>
<div class="abs nav" style="left:808px">Driving Directions</div>
<div class="abs btn" style="left:960px;top:20px;width:128px;height:46px;font-size:16px"><span>Contact Us</span></div>

<!-- hero -->
<section class="abs hero" role="img" aria-label="Aerial view of a white motor yacht cutting through deep blue water"></section>
<h1 class="abs hero" style="background:none;height:auto;width:auto">
</h1>
<h1 class="abs" style="left:110px;top:198px;font-family:'Chakra Petch',sans-serif;font-weight:700;font-size:56px;line-height:64px;color:#fff">Welcome to<br>Garland Boats.</h1>
<p class="abs" style="left:110px;top:330px;width:480px;font-size:17px;line-height:28px;color:#fff">We build custom boats to meet our customers' specification. Our boats range in size from 26' to 71'.</p>
<div class="abs btn" style="left:112px;top:402px;width:128px;height:44px;background:var(--red)"><span>Get Started</span></div>
<svg class="abs" style="left:0;top:590px" width="1200" height="45" viewBox="0 0 1200 45">
  <path d="M0 45 C300 10 900 10 1200 45 Z" fill="#fff"/>
  <path d="M230 28 C500 5 700 5 960 28 C700 45 500 45 230 28 Z" fill="#c8202a"/>
</svg>

<!-- about -->
<div class="abs photo" style="left:126px;top:735px;width:443px;height:423px;box-shadow:0 6px 16px rgba(0,0,0,.2)" role="img" aria-label="White luxury yacht under way on open sea"></div>
<h2 class="abs heading" style="left:639px;top:732px">ABOUT <span class="accent">US</span></h2>
<div class="abs underline" style="left:639px;top:784px"></div>
<p class="abs body-text" style="left:639px;top:810px;width:448px"><em style="font-weight:600">Garland Custom Boats</em> is a premier manufacturer of custom boats, specializing in the creation of high-quality vessels ranging from 28 to 72 feet in length. With a strong focus on precision and craftsmanship, we design and build boats tailored to meet the diverse needs of our clients. Our portfolio spans a wide array of markets, featuring everything from sleek recreational fishing boats, ready for adventures on the water, to robust commercial diving vessels designed to thrive in the toughest conditions. Regardless of the purpose, each boat is a testament to our commitment to excellence and innovation in marine design.</p>
<div class="abs btn" style="left:641px;top:1111px;width:128px;height:47px"><span>Read More</span></div>

<!-- our boats -->
<svg class="abs" style="left:0;top:1267px" width="1200" height="646" viewBox="0 0 1200 646">
  <path d="M0 0 H1200 V420 C1200 560 1100 646 940 646 H0 Z" fill="#0b44a8"/>
</svg>
<h2 class="abs heading" style="left:0;width:1200px;text-align:center;top:1345px;color:#fff">OUR BOATS</h2>
<div class="abs underline" style="left:520px;top:1396px"></div>
<div class="abs card photo" style="left:110px;top:1452px" role="img" aria-label="Dive boat anchored in turquoise water"></div>
<div class="abs card photo" style="left:449px;top:1452px" role="img" aria-label="Sport fisherman yacht running fast across the water"></div>
<div class="abs card" style="left:786px;top:1452px;background:linear-gradient(180deg,#e8d8bf,#8a8f8f 60%,#3e4a52)" role="img" aria-label="Grey patrol boat at sea"></div>
<div class="abs label" style="left:110px;top:1765px">Dive Boats</div>
<div class="abs label" style="left:449px;top:1765px">Yacht Sport Fisherman</div>
<div class="abs label" style="left:786px;top:1765px">Patrol Boats</div>

<!-- research vessels -->
<h2 class="abs heading" style="left:112px;top:2033px">RESEARCH <span class="accent">VESSELS</span></h2>
<div class="abs underline" style="left:112px;top:2084px"></div>
<p class="abs body-text" style="left:112px;top:2117px;width:455px">we specialize in durable supply boats essential for efficient logistics in remote areas. Our buoy tender boats, designed for the National Marine Monitoring Office (NMMO), aid in the maintenance and deployment of buoys that are critical for environmental monitoring.<br><br>Furthermore, we create specialized dive boats customized for specific regions, ensuring they meet the unique demands of local diving activities.</p>
<div class="abs btn" style="left:114px;top:2378px;width:128px;height:47px"><span>Read More</span></div>
<div class="abs" style="left:620px;top:2020px;width:443px;height:405px;background:linear-gradient(160deg,#2f6a58,#1d4d40 60%,#163b33);box-shadow:0 6px 16px rgba(0,0,0,.2)" role="img" aria-label="Video still of a center console boat running over green water"></div>
<svg class="abs" style="left:808px;top:2189px" width="66" height="66" viewBox="0 0 66 66">
  <circle cx="33" cy="33" r="32" fill="#fff"/><circle cx="33" cy="33" r="26" fill="#111"/>
  <path d="M27 22 L46 33 L27 44 Z" fill="#fff"/>
</svg>

<!-- partners -->
<section class="abs" style="left:0;top:2532px;width:1200px;height:503px;background:var(--pale)"></section>
<h2 class="abs heading" style="left:0;width:1200px;text-align:center;top:2622px">OUR <span class="accent">PARTNERS</span></h2>
<div class="abs underline" style="left:520px;top:2673px"></div>
<div class="abs partner" style="left:143px;top:2717px"><i></i></div>
<div class="abs partner" style="left:383px;top:2717px"><i></i></div>
<div class="abs partner" style="left:624px;top:2717px"><i></i></div>
<div class="abs partner" style="left:864px;top:2717px"><i></i></div>
<div class="abs partner" style="left:263px;top:2837px"><i></i></div>
<div class="abs partner" style="left:503px;top:2837px"><i></i></div>
<div class="abs partner" style="left:744px;top:2837px"><i></i></div>

<!-- contact -->
<h2 class="abs heading" style="left:0;width:1200px;text-align:center;top:3114px">CONTACT <span class="accent">US</span></h2>
<div class="abs underline" style="left:520px;top:3165px"></div>
<div class="abs field" style="left:182px;top:3205px;width:411px;height:50px">Name</div>
<div class="abs field" style="left:606px;top:3205px;width:411px;height:50px">Email</div>
<div class="abs field" style="left:182px;top:3268px;width:411px;height:50px">Phone Number</div>
<div class="abs field" style="left:606px;top:3268px;width:411px;height:50px">Subject</div>
<div class="abs field" style="left:182px;top:3330px;width:835px;height:88px">Message</div>
<div class="abs btn" style="left:532px;top:3440px;width:134px;height:50px;font-family:'Figtree',sans-serif;font-size:16px"><span>Submit</span></div>

<!-- footer -->
<section class="abs footer"></section>
<svg class="abs" style="left:0;top:3560px" width="1200" height="45" viewBox="0 0 1200 45">
  <path d="M0 0 H1200 V30 C900 0 300 0 0 30 Z" fill="#fff"/>
  <path d="M230 18 C500 0 700 0 960 18 C700 40 500 40 230 18 Z" fill="#c8202a"/>
</svg>
<div class="abs" style="left:110px;top:3722px;font-family:'Chakra Petch',sans-serif;font-weight:700;font-size:34px;color:#fff;line-height:1">GARLAND<div style="font-size:15px;letter-spacing:3px;font-weight:600;margin-top:6px">CUSTOM BOATS</div></div>
<div class="abs social" style="left:152px;top:3814px;background:var(--red);border-color:var(--red)"></div>
<div class="abs social" style="left:189px;top:3814px"></div>
<div class="abs social" style="left:226px;top:3814px"></div>
<div class="abs social" style="left:263px;top:3814px"></div>

<div class="abs ftitle" style="left:453px;top:3685px">Quick Links</div>
<div class="abs" style="left:453px;top:3718px">
  <div class="flink"><svg width="14" height="12" viewBox="0 0 14 12"><path d="M0 6 H11 M7 1 L12 6 L7 11" stroke="#fff" stroke-width="2.4" fill="none"/></svg>Home</div>
  <div class="flink"><svg width="14" height="12" viewBox="0 0 14 12"><path d="M0 6 H11 M7 1 L12 6 L7 11" stroke="#fff" stroke-width="2.4" fill="none"/></svg>About Us</div>
  <div class="flink"><svg width="14" height="12" viewBox="0 0 14 12"><path d="M0 6 H11 M7 1 L12 6 L7 11" stroke="#fff" stroke-width="2.4" fill="none"/></svg>Services</div>
  <div class="flink"><svg width="14" height="12" viewBox="0 0 14 12"><path d="M0 6 H11 M7 1 L12 6 L7 11" stroke="#fff" stroke-width="2.4" fill="none"/></svg>Solutions</div>
  <div class="flink"><svg width="14" height="12" viewBox="0 0 14 12"><path d="M0 6 H11 M7 1 L12 6 L7 11" stroke="#fff" stroke-width="2.4" fill="none"/></svg>Blog</div>
  <div class="flink"><svg width="14" height="12" viewBox="0 0 14 12"><path d="M0 6 H11 M7 1 L12 6 L7 11" stroke="#fff" stroke-width="2.4" fill="none"/></svg>Contact Us</div>
</div>

<div class="abs ftitle" style="left:651px;top:3685px">Other Links</div>
<div class="abs" style="left:651px;top:3716px">
  <div class="flink"><svg width="14" height="12" viewBox="0 0 14 12"><path d="M0 6 H11 M7 1 L12 6 L7 11" stroke="#fff" stroke-width="2.4" fill="none"/></svg>FAQ</div>
  <div class="flink"><svg width="14" height="12" viewBox="0 0 14 12"><path d="M0 6 H11 M7 1 L12 6 L7 11" stroke="#fff" stroke-width="2.4" fill="none"/></svg>Tems of Use</div>
  <div class="flink"><svg width="14" height="12" viewBox="0 0 14 12"><path d="M0 6 H11 M7 1 L12 6 L7 11" stroke="#fff" stroke-width="2.4" fill="none"/></svg>Privacy Policy</div>
  <div class="flink"><svg width="14" height="12" viewBox="0 0 14 12"><path d="M0 6 H11 M7 1 L12 6 L7 11" stroke="#fff" stroke-width="2.4" fill="none"/></svg>Support Links</div>
  <div class="flink"><svg width="14" height="12" viewBox="0 0 14 12"><path d="M0 6 H11 M7 1 L12 6 L7 11" stroke="#fff" stroke-width="2.4" fill="none"/></svg>Conditions</div>
</div>

<div class="abs ftitle" style="left:855px;top:3685px">Contact Us</div>
<div class="abs ficon" style="left:857px;top:3730px"><svg width="14" height="18" viewBox="0 0 14 18"><path d="M7 0 C3 0 0 3 0 7 C0 12 7 18 7 18 C7 18 14 12 14 7 C14 3 11 0 7 0 Z" fill="#fff"/><circle cx="7" cy="7" r="2.5" fill="#c8202a"/></svg></div>
<div class="abs" style="left:906px;top:3729px;font-size:15px;line-height:20px;color:#fff">All Boats are FOB Bayport,<br>Gulf Coast USA</div>
<div class="abs ficon" style="left:857px;top:3795px"><svg width="16" height="12" viewBox="0 0 16 12"><rect width="16" height="12" rx="1.5" fill="#fff"/><path d="M1 1 L8 7 L15 1" stroke="#c8202a" stroke-width="1.5" fill="none"/></svg></div>
<div class="abs" style="left:906px;top:3803px;font-size:15px;color:#fff">info@garlandboats.com</div>
<div class="abs ficon" style="left:857px;top:3853px"><svg width="16" height="16" viewBox="0 0 16 16"><path d="M3 1 L6 1 L7 5 L5 6.5 C6 9 7 10 9.5 11 L11 9 L15 10 L15 13 C15 14 14 15 13 15 C6 15 1 10 1 3 C1 2 2 1 3 1 Z" fill="#fff"/></svg></div>
<div class="abs" style="left:906px;top:3861px;font-size:15px;color:#fff">555.014.2290</div>

<div class="abs" style="left:98px;top:3955px;width:1004px;height:1px;background:#555"></div>
<div class="abs" style="left:0;width:1200px;text-align:center;top:3980px;font-size:14px;color:#fff">Copyrights@2025.Garland Custom Boats.All Rights Reserved</div>

</body>
</html>
```